Business Cards/Stationery - Information Technology Company
Dorian Welk Consulting, An Information Technology Services Company
Business Cards/Stationery - Information Technology Company - Information Technology
Creative Brief
Use specific fonts
Whatever works the best.
Simple
Dorian Welk
Solutions Architect & Owner
782 Birchwood Lane Suite 205 Glen Ellyn, IL 60298-3817
dorianwelk@mailbox-example.net
http://dorianwelk-example.net
Please use the tagline: "An Information Technology Services Company" under the logo on cards, letterhead, and envelope.
dorianwelk dorianwelk
Sorry about the long delay. I will be selecting a finalist in the next day.
The NPDA uses the bottom 1/2" of envelopes and prints a black barcode and text when processing. This area should be either be left blank or printed with very light colors or watermark. Designs can have printing on the bottom 1/2" of envelopes as long as it is light enough that NPDA can print its black barcode and it will be visible.
I will rate all designs very soon. Thanks for your patience.
QUIKPIXLER QUIKPIXLER
Star rating please,,,
The two color logo in .ai format has been uploaded and is now available to designers. Sorry about the delay.
The two logo in .ai format has been uploaded and is now available to designers. Sorry about the delay.
I really like the two sided designs that have been submitted so far. I didn't originally plan on a two sided design, but I have changed my mind thanks to all the designer's excellent work. PLEASE SUBMIT ALL FUTURE DESIGNS AS TWO SIDED. Thanks!
tenriver tenriver
Please upload Ai file of your logo!! thnks
I just uploaded the two color version of the logo in .jpg format. I also have .psd and .tif formats available. I don't have an .ai version, but I can get if needed. Please use the two color logo version and let me know if you need anything else. Thanks!

```html
<!DOCTYPE html>
<html lang="en">
<head>
<meta charset="utf-8">
<title>Dorian Welk Consulting — Stationery</title>
<link rel="stylesheet" href="https://fonts.googleapis.com/css2?family=Open+Sans:wght@400;600;700&display=swap">
<style>
  :root {
    --bg: #e6e7ea;
    --paper: #ffffff;
    --navy: #2b3f86;
    --stripe: #c9cfe2;
    --ink: #4a4d55;
    --muted: #8a8d94;
    --shadow: 0 6px 18px rgba(0,0,0,.12);
  }
  * { box-sizing: border-box; margin: 0; padding: 0; }
  html, body { width: 1200px; height: 961px; overflow: hidden; }
  body {
    background: var(--bg);
    font-family: "Open Sans", Arial, sans-serif;
    color: var(--ink);
    position: relative;
  }
  .sheet { position: absolute; background: var(--paper); box-shadow: var(--shadow); overflow: hidden; }

  .brand { display: flex; align-items: flex-start; gap: 8px; }
  .brand-mark { background: var(--navy); flex: none; }
  .brand-name { color: var(--navy); font-weight: 600; line-height: 1.05; }
  .tagline { color: var(--muted); font-size: 7px; margin-top: 5px; letter-spacing: .1px; white-space: nowrap; }

  .footer-band {
    position: absolute; left: 0; right: 0; bottom: 0;
    background: var(--navy);
    border-top: 4px solid var(--stripe);
    color: #fff; font-size: 11px; letter-spacing: .6px;
    display: flex; align-items: center; padding-left: 28px;
  }

  /* Letterhead */
  .letterhead { left: 60px; top: 113px; width: 520px; height: 735px; }
  .letterhead .brand { position: absolute; left: 40px; top: 40px; }
  .letterhead .brand-mark { width: 26px; height: 26px; }
  .letterhead .brand-name { font-size: 16px; }
  .letterhead .address {
    position: absolute; right: 40px; top: 120px; width: 170px;
    font-size: 8px; line-height: 1.6; color: var(--ink);
  }
  .contact-line { display: flex; align-items: center; gap: 5px; }
  .contact-line svg { flex: none; }
  .letterhead .footer-band { height: 48px; }

  /* Envelope */
  .envelope { left: 640px; top: 113px; width: 500px; height: 250px; }
  .envelope .brand { position: absolute; left: 26px; top: 26px; }
  .envelope .brand-mark { width: 22px; height: 22px; }
  .envelope .brand-name { font-size: 13px; }
  .envelope .address { position: absolute; right: 40px; top: 128px; font-size: 8px; line-height: 1.6; }
  .envelope .footer-band { height: 34px; font-size: 10px; }

  /* Cards */
  .card { width: 240px; height: 140px; }
  .card-front { left: 640px; top: 400px; }
  .card-back { left: 900px; top: 400px; background: var(--navy); }
  .card-front .brand { position: absolute; left: 16px; top: 16px; }
  .card-front .brand-mark { width: 16px; height: 16px; }
  .card-front .brand-name { font-size: 10px; }
  .card-front .tagline { font-size: 5.5px; margin-top: 3px; }
  .card-front .person { position: absolute; left: 16px; bottom: 16px; }
  .person-name { font-size: 9px; font-weight: 700; color: var(--navy); }
  .person-title { font-size: 6.5px; color: var(--muted); }
  .card-front .details { position: absolute; right: 16px; bottom: 16px; font-size: 6px; line-height: 1.6; text-align: right; }
  .card-back .brand { position: absolute; left: 50%; top: 50%; transform: translate(-50%,-50%); align-items: center; flex-direction: column; text-align: center; gap: 6px; }
  .card-back .brand-mark { width: 18px; height: 18px; background: #fff; }
  .card-back .brand-name { color: #fff; font-size: 12px; white-space: nowrap; }
  .card-back .tagline { color: var(--stripe); font-size: 6px; margin-top: 0; }
</style>
</head>
<body>

<section class="sheet letterhead" aria-label="Letterhead">
  <div class="brand">
    <span class="brand-mark"></span>
    <div>
      <div class="brand-name">Dorian Welk<br>Consulting</div>
      <div class="tagline">An Information Technology Services Company</div>
    </div>
  </div>
  <div class="address">
    782 Birchwood Lane<br>Suite 205<br>Harlow Springs, WI 54821-3817
    <div class="contact-line">
      <svg width="7" height="7" viewBox="0 0 10 10"><path d="M2 1l2 2-1 1.5a6 6 0 0 0 2.5 2.5L7 6l2 2-1.5 1.5C4 9 1 6 .5 2.5z" fill="#2b3f86"/></svg>
      555.201.0142
    </div>
    <div class="contact-line">
      <svg width="7" height="7" viewBox="0 0 10 10"><rect x=".5" y="2" width="9" height="6" fill="none" stroke="#2b3f86"/><path d="M.5 2l4.5 3.5L9.5 2" fill="none" stroke="#2b3f86"/></svg>
      dorianwelk@mailbox-example.net
    </div>
  </div>
  <div class="footer-band">www.dorianwelk-example.net</div>
</section>

<section class="sheet envelope" aria-label="Envelope">
  <div class="brand">
    <span class="brand-mark"></span>
    <div>
      <div class="brand-name">Dorian Welk<br>Consulting</div>
      <div class="tagline">An Information Technology Services Company</div>
    </div>
  </div>
  <div class="address">782 Birchwood Lane<br>Suite 205<br>Harlow Springs, WI 54821-3817</div>
  <div class="footer-band">www.dorianwelk-example.net</div>
</section>

<section class="sheet card card-front" aria-label="Business card front">
  <div class="brand">
    <span class="brand-mark"></span>
    <div>
      <div class="brand-name">Dorian Welk<br>Consulting</div>
      <div class="tagline">An Information Technology Services Company</div>
    </div>
  </div>
  <div class="person">
    <div class="person-name">Dorian Welk</div>
    <div class="person-title">Solutions Architect &amp; Owner</div>
  </div>
  <div class="details">
    782 Birchwood Lane, Suite 205<br>Harlow Springs, WI 54821-3817<br>555.201.0142<br>dorianwelk@mailbox-example.net
  </div>
</section>

<section class="sheet card card-back" aria-label="Business card back">
  <div class="brand">
    <span class="brand-mark"></span>
    <div class="brand-name">Dorian Welk Consulting</div>
    <div class="tagline">An Information Technology Services Company</div>
  </div>
</section>

</body>
</html>
```